Insert card for anti-slip sticker

Product packaging should be inspired by the following
packaging and stand out at the same time: https://bxlo.example/7QwRtvk

The packaging is not packaging in the conventional sense, but rather a kind of insert card that can be opened.
This can also be found in the linked product.

On the front of the card: Product name (20 anti-slip strips), advantages of the product and a appealing picture with the product

Inside: Instructions for use and product tips

Back: Images with possible uses, company headquarters, email for contact purposes, note about positive evaluation on Veltora

```html
<!DOCTYPE html>
<html lang="en">
<head>
<meta charset="utf-8">
<title>Anti-Slip Strips Insert Card</title>
<link rel="stylesheet" href="https://fonts.googleapis.com/css2?family=Cormorant+Garamond:wght@300;400;500&family=Jost:wght@300;400&display=swap">
<style>
:root{
  --stage:#6d6e71;
  --paper:#ffffff;
  --gold:#c69a45;
  --gold-light:#d9b46a;
  --ink:#1f1f1f;
  --ink-soft:#3a3a3a;
  --night-edge:#7a7a7a;
  --label:#ffffff;
}
*{margin:0;padding:0;box-sizing:border-box}
html,body{width:1200px;height:924px;overflow:hidden;background:var(--stage)}
body{position:relative;font-family:"Jost",sans-serif;color:var(--ink)}
.serif,.count-num,.count-words,.specs-title,.benefit-label,.brand,.panel-label{font-variant-numeric:lining-nums}
.panel-label{position:absolute;top:121px;font-family:"Cormorant Garamond",serif;font-size:8.5px;letter-spacing:.5px;color:var(--label)}
.spread{position:absolute;top:138px;width:449px;height:672px;box-shadow:0 3px 8px rgba(0,0,0,.35)}
.spread--outer{left:123px}
.spread--inner{left:642px}
.spread-art{position:absolute;inset:0}
.abs{position:absolute}
.serif{font-family:"Cormorant Garamond",serif}
.count{display:flex;align-items:center;position:absolute}
.count-num{font-family:"Cormorant Garamond",serif;font-weight:300;color:var(--gold);line-height:1}
.count-rule{width:1px;background:var(--ink-soft);margin:0 7px}
.count-words{font-family:"Cormorant Garamond",serif;line-height:1;letter-spacing:.6px}
.pill{position:absolute;border:1px solid var(--gold);border-radius:10px;display:flex;align-items:center;justify-content:center;font-size:7px;letter-spacing:.4px}
.contact{position:absolute;left:15px;display:flex;align-items:center;gap:6px;color:#fff;font-size:8.4px}
.contact-icon{width:12px;height:12px}
.benefit-label{position:absolute;width:84px;text-align:center;font-family:"Cormorant Garamond",serif;font-size:9.5px;color:var(--ink-soft);left:223px}
.brand{position:absolute;left:283px;top:518px;width:130px;text-align:center;font-family:"Cormorant Garamond",serif;font-size:22px;font-weight:400;color:var(--gold)}
.tips{position:absolute;left:17px;top:168px;width:205px;list-style:none}
.tips li{position:relative;padding-left:11px;font-size:7.9px;line-height:12.3px;color:var(--ink-soft);margin-bottom:12px}
.tips li::before,.specs li::before{content:"";position:absolute;left:0;top:3px;width:6px;height:6px;border:1px solid var(--gold);border-radius:50%}
.specs-title{position:absolute;left:27px;top:369px;font-family:"Cormorant Garamond",serif;font-size:17px;letter-spacing:1px;color:var(--gold-light)}
.specs{position:absolute;left:27px;top:402px;list-style:none}
.specs li{position:relative;padding-left:16px;font-size:11px;line-height:19.5px;color:var(--ink-soft)}
.specs li::before{top:5px;width:8px;height:8px}
.step{position:absolute;left:349px;font-size:9.4px;line-height:12.8px;color:var(--ink-soft)}
.step-title{color:var(--gold);letter-spacing:.4px}
</style>
</head>
<body>

<span class="panel-label" style="left:137px">BACK</span>
<span class="panel-label" style="left:402px">FRONT</span>
<span class="panel-label" style="left:654px">INSIDE LEFT</span>
<span class="panel-label" style="left:920px">INSIDE RIGHT</span>

<section class="spread spread--outer">
  <svg class="spread-art" width="449" height="672" viewBox="0 0 449 672">
    <defs>
      <linearGradient id="marbleA" x1="0" y1="0" x2="1" y2="1">
        <stop offset="0" stop-color="#ffffff"/><stop offset=".5" stop-color="#f3f2ef"/><stop offset="1" stop-color="#ffffff"/>
      </linearGradient>
      <linearGradient id="goldA" x1="0" y1="0" x2="1" y2="0">
        <stop offset="0" stop-color="#a87c2e"/><stop offset=".5" stop-color="#f0d38c"/><stop offset="1" stop-color="#b88a38"/>
      </linearGradient>
      <linearGradient id="nightA" x1="0" y1="0" x2="0" y2="1">
        <stop offset="0" stop-color="#3a3a3a"/><stop offset="1" stop-color="#0e0e0e"/>
      </linearGradient>
      <linearGradient id="legsPhoto" x1="0" y1="0" x2="1" y2="1">
        <stop offset="0" stop-color="#7d7b78"/><stop offset=".45" stop-color="#c5a795"/><stop offset="1" stop-color="#a9a39d"/>
      </linearGradient>
      <linearGradient id="seamA" x1="0" y1="0" x2="1" y2="0">
        <stop offset="0" stop-color="#000" stop-opacity="0"/><stop offset="1" stop-color="#000" stop-opacity=".12"/>
      </linearGradient>
    </defs>
    <rect width="449" height="672" fill="url(#marbleA)"/>
    <rect x="200" width="28" height="672" fill="url(#seamA)"/>
    <path d="M177,0 H228 V150 Q195,80 177,0 Z" fill="#8d8b88" role="img" aria-label="Photo of a bathroom wall"/>
    <path d="M228,0 H449 V455 C400,490 300,480 228,445 Z" fill="url(#legsPhoto)" role="img" aria-label="Photo of a woman stepping out of a bathtub onto anti-slip strips"/>
    <path d="M177,0 Q250,190 449,222" fill="none" stroke="url(#goldA)" stroke-width="3"/>

    <g stroke="url(#goldA)" stroke-width="2">
      <circle cx="60" cy="293" r="37" fill="#c2bcb6" role="img" aria-label="Photo of feet on a shower floor"/>
      <circle cx="121" cy="339" r="59" fill="#8f8f8f" role="img" aria-label="Photo of a foot on strips in a tub"/>
      <circle cx="167" cy="405" r="37" fill="#b8aa98" role="img" aria-label="Photo of a strip on a stair step"/>
    </g>

    <g fill="#0d0d0d" stroke="url(#goldA)" stroke-width="2">
      <circle cx="265" cy="256" r="27"/>
      <circle cx="265" cy="332" r="27"/>
      <circle cx="265" cy="405" r="27"/>
    </g>
    <path d="M254,256 l7,8 l14,-16" fill="none" stroke="#fff" stroke-width="3"/>
    <path d="M265,318 C259,328 255,334 255,339 a10,10 0 0 0 20,0 C275,334 271,328 265,318 Z" fill="#fff"/>
    <path d="M256,405 h18 M265,396 v18" stroke="#fff" stroke-width="3"/>

    <circle cx="348" cy="499" r="17" fill="none" stroke="url(#goldA)" stroke-width="1.5"/>

    <path d="M0,555 Q150,560 247,672 H0 Z" fill="url(#nightA)"/>
    <path d="M0,555 Q150,560 247,672" fill="none" stroke="var(--night-edge)" stroke-width="3"/>
    <path d="M228,672 Q320,565 449,558 V672 Z" fill="url(#nightA)"/>
    <path d="M228,672 Q320,565 449,558" fill="none" stroke="var(--night-edge)" stroke-width="3"/>
  </svg>

  <div class="count" style="left:76px;top:169px">
    <span class="count-num" style="font-size:45px">20</span>
    <span class="count-rule" style="height:36px"></span>
    <span class="count-words" style="font-size:16px;color:var(--gold)">ANTI-SLIP<br><span style="font-size:20px">STRIPS</span></span>
  </div>
  <div class="abs serif" style="left:24px;top:478px;font-size:20.5px;letter-spacing:1px;color:var(--ink)">ANTI SLIP STICKER</div>
  <div class="pill" style="left:34px;top:522px;width:161px;height:19px;color:var(--ink)">BATH / SHOWER / TUB / WET AREA</div>

  <div class="contact" style="top:608px">
    <svg class="contact-icon" viewBox="0 0 12 12"><circle cx="6" cy="6" r="5.4" fill="none" stroke="var(--gold)"/><path d="M4,3.3 l1,1.4 -0.6,0.8 c0.4,0.9 1,1.5 1.9,1.9 l0.8,-0.6 1.4,1 -0.6,1 c-2.4,-0.3 -4.3,-2.2 -4.6,-4.6 z" fill="var(--gold)"/></svg>
    012 555 0148
  </div>
  <div class="contact" style="top:626px">
    <svg class="contact-icon" viewBox="0 0 12 12"><circle cx="6" cy="6" r="5.4" fill="none" stroke="var(--gold)"/><rect x="3.2" y="4" width="5.6" height="4" fill="none" stroke="var(--gold)" stroke-width=".8"/><path d="M3.2,4 L6,6.2 8.8,4" fill="none" stroke="var(--gold)" stroke-width=".8"/></svg>
    hello@gripstrip.example
  </div>
  <div class="contact" style="top:644px">
    <svg class="contact-icon" viewBox="0 0 12 12"><circle cx="6" cy="6" r="5.4" fill="none" stroke="var(--gold)"/><circle cx="6" cy="6" r="3" fill="none" stroke="var(--gold)" stroke-width=".8"/><path d="M3,6 h6 M6,3 c-1.4,1.6 -1.4,4.4 0,6 c1.4,-1.6 1.4,-4.4 0,-6" fill="none" stroke="var(--gold)" stroke-width=".7"/></svg>
    www.gripstrip.example
  </div>

  <div class="benefit-label" style="top:286px">100% Non-Slip</div>
  <div class="benefit-label" style="top:362px">Water Repellent</div>
  <div class="benefit-label" style="top:434px">Easy Assembly</div>

  <div class="brand">Mira Vale</div>

  <div class="count" style="left:323px;top:596px">
    <span class="count-num" style="font-size:38px">20</span>
    <span class="count-rule" style="height:30px;background:var(--gold)"></span>
    <span class="count-words" style="font-size:12px;color:var(--gold)">ANTI-SLIP<br><span style="font-size:16px">STRIPS</span></span>
  </div>
  <div class="pill" style="left:275px;top:639px;width:162px;height:19px;color:#fff">BATH / SHOWER / TUB / WET AREA</div>
</section>

<section class="spread spread--inner">
  <svg class="spread-art" width="449" height="672" viewBox="0 0 449 672">
    <defs>
      <linearGradient id="marbleB" x1="0" y1="0" x2="1" y2="1">
        <stop offset="0" stop-color="#ffffff"/><stop offset=".5" stop-color="#f3f2ef"/><stop offset="1" stop-color="#ffffff"/>
      </linearGradient>
      <linearGradient id="goldB" x1="0" y1="0" x2="1" y2="0">
        <stop offset="0" stop-color="#a87c2e"/><stop offset=".5" stop-color="#f0d38c"/><stop offset="1" stop-color="#b88a38"/>
      </linearGradient>
      <linearGradient id="nightB" x1="0" y1="0" x2="0" y2="1">
        <stop offset="0" stop-color="#3a3a3a"/><stop offset="1" stop-color="#0e0e0e"/>
      </linearGradient>
      <linearGradient id="showerPhoto" x1="0" y1="0" x2="1" y2="1">
        <stop offset="0" stop-color="#6b655d"/><stop offset=".5" stop-color="#9a7443"/><stop offset="1" stop-color="#c29a5c"/>
      </linearGradient>
      <linearGradient id="stripsArea" x1="0" y1="0" x2="0" y2="1">
        <stop offset="0" stop-color="#e6e6e6"/><stop offset="1" stop-color="#f2f2f2"/>
      </linearGradient>
      <linearGradient id="seamB" x1="0" y1="0" x2="1" y2="0">
        <stop offset="0" stop-color="#000" stop-opacity="0"/><stop offset="1" stop-color="#000" stop-opacity=".12"/>
      </linearGradient>
    </defs>
    <rect width="449" height="672" fill="url(#marbleB)"/>
    <rect x="196" width="28" height="672" fill="url(#seamB)"/>
    <path d="M95,0 H224 V88 Q150,60 95,0 Z" fill="#9a9a9a" role="img" aria-label="Photo of a bathroom wall"/>
    <path d="M224,0 H449 V256 Q390,300 224,233 Z" fill="url(#showerPhoto)" role="img" aria-label="Photo of a glass shower with a wooden floor and anti-slip strips"/>
    <path d="M95,0 Q250,112 449,158" fill="none" stroke="url(#goldB)" stroke-width="3"/>
    <circle cx="393" cy="226" r="46" fill="none" stroke="#fff" stroke-width="3"/>

    <line x1="17" y1="134" x2="191" y2="134" stroke="url(#goldB)" stroke-width="1"/>

    <rect x="14" y="483" width="200" height="130" rx="6" fill="url(#stripsArea)" role="img" aria-label="Technical drawing of the twenty strips with their 45 by 2 cm size"/>

    <g stroke="url(#goldB)" stroke-width="2">
      <circle cx="291" cy="324" r="39" fill="#b8b4ae" role="img" aria-label="Photo of hands peeling a strip"/>
      <circle cx="287" cy="436" r="39" fill="#a9a49d" role="img" aria-label="Photo of a strip being lifted from its backing"/>
      <circle cx="289" cy="554" r="39" fill="#9f9a94" role="img" aria-label="Photo of a hand pressing a strip in place"/>
    </g>
    <g fill="#0d0d0d" stroke="#fff" stroke-width="1.2">
      <circle cx="321" cy="309" r="12"/>
      <circle cx="324" cy="414" r="12"/>
      <circle cx="322" cy="536" r="12"/>
    </g>
    <g fill="#fff" font-family="Jost, sans-serif" font-size="11" text-anchor="middle">
      <text x="321" y="313">1</text>
      <text x="324" y="418">2</text>
      <text x="322" y="540">3</text>
    </g>

    <path d="M0,672 Q224,586 449,672 Z" fill="url(#nightB)"/>
  </svg>

  <div class="count" style="left:17px;top:94px">
    <span class="count-num" style="font-size:40px">20</span>
    <span class="count-rule" style="height:28px"></span>
    <span class="count-words" style="font-size:12px;color:var(--ink)">ANTI-SLIP<br><span style="font-size:16px">STRIPS</span></span>
  </div>

  <ul class="tips">
    <li>Non-slip strips, anti-slip stair steps.</li>
    <li>Kindra children's bath with shower, bath mat, wooden bathroom set, parts, child safety stairs, bath mat, black stair steps, anti-slip rubber mat, washing machine baby mat, bath accessory, children's bath mat.</li>
    <li>Children's non-slip transparent mat, baby bath anti-slip mat, bathroom accessories set.</li>
    <li>Anti-slip stair steps, adhesive tape for stair steps, tile, granite, stair steps, non-slip steps</li>
  </ul>

  <div class="specs-title">20 ANTI-SLIP STRIPS</div>
  <ul class="specs">
    <li>Non-Slip Strips 45 x 2 cm</li>
    <li>Transparent Non-Slip</li>
    <li>Bath and Shower Stairs</li>
  </ul>

  <div class="step" style="top:312px"><div class="step-title">STEP 1</div>Self adhesive<br>anti-slip strips</div>
  <div class="step" style="top:419px"><div class="step-title">STEP 2</div>Quick and easy<br>to use: just peel<br>and stick</div>
  <div class="step" style="top:541px"><div class="step-title">STEP 3</div>Perfect for bathrooms,<br>stairs, decking,<br>walkways, ramps...</div>
</section>

</body>
</html>
```